STOREFRONT LIT SIGN for The Cantera Workshop

A sign advertising our music academy. This sign will be hung 10 feet above the entrance of our building and will be seen by all pedestrian and vehicle traffic on Fenwick Lane Delano.

Target Market(s)

Street passerby

Industry/Entity Type

Music Training

Font styles to use
Other font styles liked:
• Creative

Colors

Designer to choose colors to be used in the design.

Requirements
Must have
• A White Background
• Dimensions: 8 ft long x 3 ft tall
• The Cantera Workshop of Delano
• Lecciones de Piano, Violin, Guitarra, Voz, Trompeta y Mas
• MUSIC ACADEMY *(This should be most prominent)
• Guitar, Voice, Trumpet and More
• (555) 384-7291
• thecanteraworkshop.example
Nice to have
• Graphics of a piano, or guitar, or violin or trumpet or a combination of two or more

```html
<!DOCTYPE html>
<html lang="en">
<head>
<meta charset="utf-8">
<title>The Cantera Workshop – Storefront Sign Options</title>
<link rel="stylesheet" href="https://fonts.googleapis.com/css2?family=Anton&family=Bungee&family=Alfa+Slab+One&family=Montserrat:ital,wght@0,500;0,600;0,700;1,700&display=swap">
<style>
  :root {
    --board: #434446;
    --maroon: #621a33;
    --maroon-soft: #8a3a55;
    --blush: #f1e2e7;
    --white: #ffffff;
    --ink: #0b0b0b;
  }
  * { margin: 0; padding: 0; box-sizing: border-box; }
  html, body { width: 1200px; height: 1082px; overflow: hidden; background: var(--board); }
  .board { position: relative; width: 1200px; height: 1082px; }

  .option-label {
    position: absolute;
    left: 70px;
    width: 80px;
    text-align: center;
    font-family: "Bungee", sans-serif;
    font-size: 92px;
    line-height: 1;
    color: var(--white);
  }

  .sign {
    position: absolute;
    left: 230px;
    width: 843px;
    height: 317px;
    background: var(--white);
    overflow: hidden;
  }
  .sign__shapes { position: absolute; inset: 0; width: 100%; height: 100%; }

  .sign__clef {
    position: absolute; left: 16px; top: 22px; width: 80px; height: 274px;
    background: linear-gradient(180deg, var(--maroon-soft), var(--maroon));
    border-radius: 40px;
  }
  .sign__instruments {
    position: absolute; left: 640px; top: 105px; width: 139px; height: 212px;
    background: linear-gradient(160deg, var(--maroon-soft), var(--maroon));
    clip-path: polygon(58px 0, 100% 0, 100% 100%, 0 100%, 0 118px, 58px 118px);
  }
  .sign__keys {
    position: absolute; right: 0; top: 0; width: 64px; height: 100%;
    background: linear-gradient(180deg, var(--blush), #e3c6d0);
    border-left: 1px solid var(--maroon);
  }

  .sign__text {
    position: absolute; left: 433px; transform: translateX(-50%);
    white-space: nowrap; text-align: center;
  }
  .sign__name {
    top: 17px; left: 440px;
    font-family: "Montserrat", sans-serif; font-weight: 600;
    font-size: 46px; line-height: 1; color: var(--maroon);
  }
  .sign__lessons {
    top: 68px; left: 435px;
    font-family: "Montserrat", sans-serif; font-weight: 700; font-style: italic;
    font-size: 15.6px; color: var(--maroon);
  }
  .sign__headline { color: var(--ink); line-height: 1; }
  .sign__headline span { display: inline-block; }
  .sign--a .sign__headline { top: 109px; left: 434px; font-family: "Anton", sans-serif; font-size: 74px; }
  .sign--a .sign__headline span { transform: scaleX(1.12); }
  .sign--b .sign__headline { top: 102px; left: 432px; font-family: "Bungee", sans-serif; font-size: 92px; }
  .sign--b .sign__headline span { transform: scaleX(0.66); }
  .sign--c .sign__headline { top: 114px; left: 435px; font-family: "Alfa Slab One", serif; font-size: 74px; }
  .sign--c .sign__headline span { transform: scaleX(0.73); }

  .sign__services {
    top: 182px;
    font-family: "Montserrat", sans-serif; font-weight: 600;
    font-size: 28px; color: var(--ink);
  }
  .sign__phone {
    top: 227px; left: 431px;
    width: 343px; height: 51px; border-radius: 14px;
    background: var(--maroon); color: var(--white);
    font-family: "Montserrat", sans-serif; font-weight: 600;
    font-size: 42px; line-height: 51px;
  }
  .sign__web {
    top: 281px; left: 431px;
    font-family: "Montserrat", sans-serif; font-weight: 600;
    font-size: 15px; letter-spacing: 2.4px; color: var(--maroon);
  }
</style>
</head>
<body>
<main class="board">

  <div class="option-label" style="top:142px">A</div>
  <div class="option-label" style="top:482px">B</div>
  <div class="option-label" style="top:826px">C</div>

  <section class="sign sign--a" style="top:31px">
    <svg class="sign__shapes" viewBox="0 0 1054 394" preserveAspectRatio="none" aria-hidden="true">
      <path d="M0 0 H178 C215 110 215 280 90 394 H0 Z" fill="var(--maroon)"/>
      <path d="M118 0 C198 110 198 280 96 394" fill="none" stroke="var(--white)" stroke-width="7"/>
    </svg>
    <div class="sign__clef" role="img" aria-label="White treble clef illustration"></div>
    <div class="sign__instruments" role="img" aria-label="Maroon silhouettes of trumpet, guitar and violin"></div>
    <div class="sign__keys" role="img" aria-label="Vertical maroon piano keyboard"></div>
    <div class="sign__text sign__name">The Cantera Workshop</div>
    <div class="sign__text sign__lessons">Lecciones de Piano, Violin, Guitarra, Voz, Trompeta y Mas</div>
    <div class="sign__text sign__headline"><span>MUSIC ACADEMY</span></div>
    <div class="sign__text sign__services">Guitar, Voice, Trumpet and more</div>
    <div class="sign__text sign__phone">(555) 384-7291</div>
    <div class="sign__text sign__web">thecanteraworkshop.example</div>
  </section>

  <section class="sign sign--b" style="top:372px">
    <svg class="sign__shapes" viewBox="0 0 1054 394" preserveAspectRatio="none" aria-hidden="true">
      <path d="M0 0 H178 C215 110 215 280 90 394 H0 Z" fill="var(--maroon)"/>
      <path d="M118 0 C198 110 198 280 96 394" fill="none" stroke="var(--white)" stroke-width="7"/>
    </svg>
    <div class="sign__clef" role="img" aria-label="White treble clef illustration"></div>
    <div class="sign__instruments" role="img" aria-label="Maroon silhouettes of trumpet, guitar and violin"></div>
    <div class="sign__keys" role="img" aria-label="Vertical maroon piano keyboard"></div>
    <div class="sign__text sign__name">The Cantera Workshop</div>
    <div class="sign__text sign__lessons">Lecciones de Piano, Violin, Guitarra, Voz, Trompeta y Mas</div>
    <div class="sign__text sign__headline"><span>MUSIC ACADEMY</span></div>
    <div class="sign__text sign__services">Guitar, Voice, Trumpet and more</div>
    <div class="sign__text sign__phone">(555) 384-7291</div>
    <div class="sign__text sign__web">thecanteraworkshop.example</div>
  </section>

  <section class="sign sign--c" style="top:717px">
    <svg class="sign__shapes" viewBox="0 0 1054 394" preserveAspectRatio="none" aria-hidden="true">
      <path d="M0 0 H178 C215 110 215 280 90 394 H0 Z" fill="var(--maroon)"/>
      <path d="M118 0 C198 110 198 280 96 394" fill="none" stroke="var(--white)" stroke-width="7"/>
    </svg>
    <div class="sign__clef" role="img" aria-label="White treble clef illustration"></div>
    <div class="sign__instruments" role="img" aria-label="Maroon silhouettes of trumpet, guitar and violin"></div>
    <div class="sign__keys" role="img" aria-label="Vertical maroon piano keyboard"></div>
    <div class="sign__text sign__name">The Cantera Workshop</div>
    <div class="sign__text sign__lessons">Lecciones de Piano, Violin, Guitarra, Voz, Trompeta y Mas</div>
    <div class="sign__text sign__headline"><span>MUSIC ACADEMY</span></div>
    <div class="sign__text sign__services">Guitar, Voice, Trumpet and more</div>
    <div class="sign__text sign__phone">(555) 384-7291</div>
    <div class="sign__text sign__web">thecanteraworkshop.example</div>
  </section>

</main>
</body>
</html>
```